Stationery Design Project for Nimbora, Chicago

Nimbora, a street parking application which helps car drivers find a street parking spot by offering an ideal path along which to look for parking. This path is calculated by our algorithm based on data (e.g. historical data, baseball games schedule, etc.). Along this path the driver will find a spot and will also save 70% of the search time. Customer we target is reg. between 21 and 45 yo.

We envision something young, fresh, bright and original. Slightly abstract maybe. It should represent the idea and elements of finding street parking in the city, e.g. car(s), parking spot, people, city, etc. (just ideas!).

Logo is attached.

Requirement:
- Business Cards (2 Sided Full Color CMYK)
- Letterhead (1 Sided Full Color CMYK)
- Envelope (1 Sided Full Color CMYK)
- Sticker (1 Sided Full Color CMYK), round with a 2inch diameter.

Reason: We're starting to get more and more designs and need more time to look into all of them. Very exciting!! Thanks to everybody!

Hi all, we're in the process of selecting our favs. Though choices!!! Really good submissions. Will keep you posted and sorry for the delay.

Target Market(s)

Car drivers and owners between 21 and 45

Industry/Entity Type

Parking

Requirements
Must have
• Sticker should be round and include company URL nimbora.com and the new logo which we will attach soon.
Should not have
• Should not be too serious or boring.

```html
<!DOCTYPE html>
<html lang="en">
<head>
<meta charset="utf-8">
<title>Nimbora Business Card</title>
<link rel="stylesheet" href="https://fonts.googleapis.com/css2?family=Open+Sans:wght@400;600;700&display=swap">
<style>
  :root {
    --backdrop: #e9e6e2;
    --card: #ffffff;
    --card-edge: #6b6b6b;
    --ink: #333333;
    --ink-soft: #4a4a4a;
    --brand-blue: #1f5fd6;
    --brand-deep: #0b2f8a;
    --wave-light: #2f8be0;
    --band-dark: #2b2b2b;
    --band-mid: #555555;
    --rule: #bdbdbd;
  }
  * { margin: 0; padding: 0; box-sizing: border-box; }
  html, body { width: 1200px; height: 395px; overflow: hidden; }
  body {
    background: var(--backdrop);
    font-family: "Open Sans", Arial, sans-serif;
    color: var(--ink);
    position: relative;
  }
  .card {
    position: absolute;
    top: 43px;
    width: 526px;
    height: 300px;
    background: var(--card);
    border: 1px solid var(--card-edge);
    border-radius: 14px;
    overflow: hidden;
  }
  .card--front { left: 62px; }
  .card--back { left: 623px; width: 525px; }

  /* Front */
  .brand {
    position: absolute;
    left: 105px;
    top: 32px;
    display: flex;
    align-items: center;
    gap: 16px;
  }
  .brand__dot {
    width: 90px; height: 90px; border-radius: 50%;
    background: radial-gradient(circle at 40% 35%, var(--wave-light), var(--brand-blue) 55%, var(--brand-deep));
  }
  .brand__name {
    font-size: 58px;
    font-weight: 600;
    color: var(--ink-soft);
    letter-spacing: 1px;
    line-height: 1;
  }
  .address {
    position: absolute;
    right: 267px;
    top: 168px;
    text-align: right;
    font-size: 13.5px;
    line-height: 18px;
    color: var(--ink);
  }
  .divider {
    position: absolute;
    left: 273px; top: 148px;
    width: 1px; height: 80px;
    background: var(--rule);
  }
  .contacts {
    position: absolute;
    left: 287px; top: 150px;
    list-style: none;
    font-size: 13.5px;
    line-height: 19px;
  }
  .contacts li { display: flex; align-items: center; gap: 6px; }
  .contacts svg { width: 11px; height: 11px; fill: var(--ink); flex: none; }
  .wave { position: absolute; left: 0; bottom: 0; width: 526px; height: 80px; }
  .holder {
    position: absolute;
    left: 59px; bottom: 11px;
    color: #ffffff;
    font-size: 18px;
    font-weight: 700;
  }
  .holder__title { font-size: 14px; font-weight: 400; }

  /* Back */
  .mark {
    position: absolute;
    left: 184px; top: 44px;
    width: 156px; height: 156px; border-radius: 50%;
    background: radial-gradient(circle at 40% 35%, var(--wave-light), var(--brand-blue) 55%, var(--brand-deep));
    display: flex; align-items: center; justify-content: center;
    color: #ffffff; font-size: 28px; font-weight: 600;
  }
  .site {
    position: absolute;
    left: 0; right: 0; top: 250px;
    text-align: center;
    font-size: 17px;
    letter-spacing: 2px;
    color: var(--ink-soft);
  }
</style>
</head>
<body>
  <section class="card card--front">
    <div class="brand">
      <div class="brand__dot"></div>
      <div class="brand__name">nimbora</div>
    </div>

    <p class="address">Complex Name, Street Name<br>Area, City Name,000 000</p>
    <div class="divider"></div>
    <ul class="contacts">
      <li><svg viewBox="0 0 12 12"><path d="M3 1l2 2-1 1.5c.6 1.4 1.6 2.4 3 3L8.5 6.5l2 2-1.5 2C5 10 2 7 1.5 2.5z"/></svg>+1 312 555 0147</li>
      <li><svg viewBox="0 0 12 12"><path d="M3.5 0h5v12h-5zM4.5 1.5v6h3v-6z"/></svg>+1 312 555 0147</li>
      <li><svg viewBox="0 0 12 12"><path d="M1 3h10v7H1zM1 3l5 4 5-4v1L6 8 1 4z"/></svg>info@nimbora.com</li>
      <li><svg viewBox="0 0 12 12"><circle cx="6" cy="6" r="5"/></svg>www.nimbora.com</li>
    </ul>

    <svg class="wave" viewBox="0 0 526 80" preserveAspectRatio="none" aria-hidden="true">
      <defs>
        <linearGradient id="swoosh" x1="0" x2="1">
          <stop offset="0" stop-color="var(--brand-deep)"/>
          <stop offset="0.5" stop-color="var(--wave-light)"/>
          <stop offset="1" stop-color="var(--brand-deep)"/>
        </linearGradient>
        <linearGradient id="band" x1="0" x2="1">
          <stop offset="0" stop-color="var(--band-dark)"/>
          <stop offset="1" stop-color="var(--band-mid)"/>
        </linearGradient>
      </defs>
      <path d="M0 3 C120 -2 220 8 330 40 C420 58 480 50 526 30 L526 45 C470 62 400 66 330 52 C230 28 120 14 0 18 Z" fill="url(#swoosh)"/>
      <path d="M0 22 C120 18 230 34 330 56 C410 70 480 62 526 48 L526 80 L0 80 Z" fill="url(#band)"/>
    </svg>
    <p class="holder">Your Name , <span class="holder__title">Title</span></p>
  </section>

  <section class="card card--back">
    <div class="mark">nimbora</div>
    <p class="site">www.nimbora.com</p>
  </section>
</body>
</html>
```